Web Design Project for SEARCH ENGINE !

We need a website design for torrents search engine.

The Website will be www.Qentrova.com

Qentrova is a a search engine for torrents.
Qentrova search and index torrents results from all torrents sites.

We will need:
Logo
WebSite Design
slogen (optional)

we need only PSDs - no codded pages are needed !

Design to the following screen Size & resolution: 1024 x 768

***PLEASE DOWNLOAD ATTACHED FILE !

```html
<!DOCTYPE html>
<html lang="en">
<head>
<meta charset="utf-8">
<title>Qentrova — Torrent Search Engine</title>
<link href="https://fonts.googleapis.com/css2?family=Jost:wght@300;400;500&family=Arimo:wght@400&display=swap" rel="stylesheet">
<style>
  :root {
    --page-white: #ffffff;
    --bg-light: #c2c2c2;
    --bg-mid: #a9a9a9;
    --bar-top: #3a3a3a;
    --bar-bottom: #0d0d0d;
    --nav-text: #e6e6e6;
    --accent-green: #3a9a34;
    --accent-green-light: #55b548;
    --logo-grey: #5a5a5a;
    --search-field: #8c8c8c;
    --search-text: #2f2f2f;
    --dark-button: #1b1b1b;
    --popup-top: #ffffff;
    --popup-bottom: #e3e3e3;
    --label-text: #3c3c3c;
    --input-border: #8a8a8a;
    --footer-text: #d9d9d9;
    --rss: #d9771f;
    --social-blue-light: #5ea6c8;
    --social-blue-dark: #2d5d9a;
  }
  * { box-sizing: border-box; margin: 0; padding: 0; }
  html, body { width: 1200px; height: 896px; overflow: hidden; background: var(--page-white); }
  body { position: relative; font-family: "Jost", sans-serif; }

  .page {
    position: absolute; left: 7px; top: 4px; width: 1186px; height: 889px;
    background: radial-gradient(ellipse at 50% 35%, var(--bg-light) 0%, var(--bg-mid) 80%);
  }

  .top-bar, .footer-bar {
    position: absolute; left: 7px; width: 1186px;
    background: linear-gradient(var(--bar-top), var(--bar-bottom));
  }
  .top-bar { top: 4px; height: 34px; }
  .footer-bar { top: 857px; height: 36px; display: flex; align-items: center; justify-content: center; }

  .main-nav {
    position: absolute; left: 254px; top: 0; height: 34px;
    display: flex; align-items: center; gap: 12px;
    font-size: 15px; font-weight: 300; color: var(--nav-text); letter-spacing: 0.2px;
  }
  .main-nav .active { color: var(--accent-green-light); }
  .main-nav .divider { color: var(--nav-text); }

  .language-select {
    position: absolute; left: 874px; top: 7px; width: 70px; height: 21px;
    background: var(--accent-green); color: #fff;
    font-family: "Arimo", sans-serif; font-size: 12px;
    display: flex; align-items: center; justify-content: center; gap: 8px;
  }

  .brand {
    position: absolute; left: 455px; top: 148px; width: 290px; height: 82px;
  }
  .brand-mark {
    position: absolute; left: 0; top: 0; width: 57px; height: 57px;
    background: linear-gradient(var(--accent-green-light), var(--accent-green));
  }
  .brand-name {
    position: absolute; left: 66px; top: 2px;
    font-size: 50px; font-weight: 500; line-height: 1; color: var(--logo-grey);
  }
  .brand-slogan {
    position: absolute; left: 0; top: 60px;
    font-size: 22px; font-weight: 400; color: var(--logo-grey); letter-spacing: 0.5px;
  }

  .popup {
    position: absolute; left: 518px; width: 162px;
    background: linear-gradient(var(--popup-top) 40%, var(--popup-bottom));
    box-shadow: 0 0 4px rgba(0,0,0,0.35);
    font-family: "Arimo", sans-serif;
  }
  .popup-login { top: 141px; height: 198px; }
  .popup-signin { top: 478px; height: 312px; }
  .popup-title {
    position: absolute; left: 46px; top: 0; width: 70px; height: 24px;
    background: var(--dark-button); color: #fff;
    font-family: "Jost", sans-serif; font-size: 14px;
    display: flex; align-items: center; justify-content: center;
    box-shadow: 0 2px 3px rgba(0,0,0,0.4);
  }
  .popup-close { position: absolute; right: 6px; top: 4px; font-size: 11px; color: #7a4b8c; }
  .field-label { position: absolute; left: 11px; font-size: 12px; color: var(--label-text); }
  .field-input {
    position: absolute; left: 10px; width: 141px; height: 18px;
    border: 1px solid var(--input-border); background: #fff;
  }
  .check-row {
    position: absolute; left: 11px; display: flex; align-items: center; gap: 7px;
    font-size: 7px; color: var(--label-text);
  }
  .check-row a { color: var(--accent-green); text-decoration: none; }
  .checkbox {
    width: 11px; height: 11px; border: 1px solid #555; background: #fff;
    display: flex; align-items: center; justify-content: center;
  }
  .popup-button {
    position: absolute; width: 70px; height: 25px;
    background: linear-gradient(#333, var(--dark-button));
    color: #fff; font-family: "Jost", sans-serif; font-size: 14px;
    display: flex; align-items: center; justify-content: center;
    box-shadow: 0 -2px 4px rgba(255,255,255,0.6);
  }
  .popup-button.clear { left: 8px; }
  .popup-button.submit { left: 83px; }

  .search-form { position: absolute; left: 193px; top: 421px; width: 811px; height: 33px; }
  .search-field {
    position: absolute; left: 0; top: 0; width: 744px; height: 33px;
    background: var(--search-field); color: var(--search-text);
    font-family: "Arimo", sans-serif; font-size: 18px;
    display: flex; align-items: center; padding-left: 8px;
  }
  .search-button {
    position: absolute; left: 744px; top: 0; width: 67px; height: 33px;
    background: var(--dark-button); color: #fff; font-size: 11px;
    display: flex; align-items: center; justify-content: center; gap: 3px;
  }
  .search-option {
    position: absolute; right: 196px; top: 459px;
    display: flex; align-items: center; gap: 5px;
    font-family: "Arimo", sans-serif; font-size: 12px; color: #333;
  }

  .social-links { position: absolute; left: 536px; top: 798px; display: flex; gap: 24px; }
  .social-tile { width: 27px; height: 27px; border-radius: 2px; box-shadow: 0 1px 2px rgba(0,0,0,0.3); }
  .social-tile.rss { background: var(--rss); }
  .social-tile.micro { background: var(--social-blue-light); }
  .social-tile.network { background: var(--social-blue-dark); }

  .copyright { font-size: 12px; color: var(--footer-text); letter-spacing: 0.2px; }
  .copyright .link { color: var(--accent-green-light); }
</style>
</head>
<body>
  <div class="page"></div>

  <header class="top-bar">
    <nav class="main-nav">
      <span class="active">HOME</span><span class="divider">|</span>
      <span>ABOUT US</span><span class="divider">|</span>
      <span>TORRENT SEARCH</span><span class="divider">|</span>
      <span>CATEGORIES</span><span class="divider">|</span>
      <span>HELP</span><span class="divider">|</span>
      <span>LOGIN</span><span class="divider">|</span>
      <span>SIGNIN</span>
    </nav>
    <div class="language-select">English
      <svg width="8" height="6" viewBox="0 0 8 6"><path d="M0 0h8L4 6z" fill="#fff"/></svg>
    </div>
  </header>

  <div class="brand">
    <div class="brand-mark"></div>
    <div class="brand-name">Qentrova</div>
    <div class="brand-slogan">TORRENT SEARCH ENGINE</div>
  </div>

  <section class="popup popup-login">
    <div class="popup-title">LOGIN</div>
    <div class="popup-close">✕</div>
    <div class="field-label" style="top:36px">Username:</div>
    <div class="field-input" style="top:52px"></div>
    <div class="field-label" style="top:77px">Password:</div>
    <div class="field-input" style="top:93px"></div>
    <div class="check-row" style="top:121px">
      <span class="checkbox"><svg width="9" height="9" viewBox="0 0 9 9"><path d="M1 4.5l2.5 2.5L8 1.5" stroke="#222" stroke-width="1.4" fill="none"/></svg></span>
      Remember Me
    </div>
    <div class="check-row" style="top:141px">
      <span class="checkbox"><svg width="9" height="9" viewBox="0 0 9 9"><path d="M1 4.5l2.5 2.5L8 1.5" stroke="#222" stroke-width="1.4" fill="none"/></svg></span>
      <span>Forgot Your Password? <a href="#">Click here</a></span>
    </div>
    <div class="popup-button clear" style="top:173px">CLEAR</div>
    <div class="popup-button submit" style="top:173px">SUBMIT</div>
  </section>

  <div class="search-form">
    <div class="search-field">starforge 3</div>
    <div class="search-button">
      <svg width="10" height="10" viewBox="0 0 10 10"><circle cx="4" cy="4" r="3" stroke="#fff" stroke-width="1.4" fill="none"/><path d="M6 6l3.5 3.5" stroke="#fff" stroke-width="1.6"/></svg>
      SEARCH
    </div>
  </div>
  <div class="search-option">Sites search include
    <span class="checkbox"><svg width="9" height="9" viewBox="0 0 9 9"><path d="M1 4.5l2.5 2.5L8 1.5" stroke="#222" stroke-width="1.4" fill="none"/></svg></span>
  </div>

  <section class="popup popup-signin">
    <div class="popup-title">SIGNIN</div>
    <div class="popup-close">✕</div>
    <div class="field-label" style="top:43px">Username:</div>
    <div class="field-input" style="top:61px"></div>
    <div class="field-label" style="top:85px">Password:</div>
    <div class="field-input" style="top:103px"></div>
    <div class="field-label" style="top:128px">Retype Password:</div>
    <div class="field-input" style="top:148px"></div>
    <div class="field-label" style="top:170px">E-mail:</div>
    <div class="field-input" style="top:190px"></div>
    <div class="field-label" style="top:214px">Retype E-mail:</div>
    <div class="field-input" style="top:234px"></div>
    <div class="check-row" style="top:261px">
      <span class="checkbox"><svg width="9" height="9" viewBox="0 0 9 9"><path d="M1 4.5l2.5 2.5L8 1.5" stroke="#222" stroke-width="1.4" fill="none"/></svg></span>
      Agree to Privacy Policy
    </div>
    <div class="popup-button clear" style="top:287px">CLEAR</div>
    <div class="popup-button submit" style="top:287px">SUBMIT</div>
  </section>

  <div class="social-links">
    <div class="social-tile rss" role="img" aria-label="RSS feed link"></div>
    <div class="social-tile micro" role="img" aria-label="Microblog profile link"></div>
    <div class="social-tile network" role="img" aria-label="Social network page link"></div>
  </div>

  <footer class="footer-bar">
    <p class="copyright">COPYRIGHT © 2011 QENTROVA. USE OF THIS WEBSITE CONSTITUTES ACCEPTANCE OF OUR <span class="link">USER AGREEMENT</span> AND <span class="link">PRIVACY POLICY</span>.</p>
  </footer>
</body>
</html>
```